Need Help having my business card stand out

I am the owner of Birchway Canine Training and would like for my business cards to stand out. I have been trying to keep designing them myself but I can't get what I have in my head on the card. I will try my best to post templates that I like for inspirations. I want something unique but elegant. I don't want in to look cartoony or cheesy. It needs to pop in a pet shop but also in a coffee shop or gym.

Target Market(s)

Dog owners, Married ,No young kids Jr High school kids and up (maybe kids on the way) Executives, Stay at home moms/wives, Small business owners

Industry/Entity Type

Dog Training

Contact Information for Business Card

Lowell Spratt, 281-904-3376, info@birchwaycanine.example, www.birchwaycanine.example

Colors

Designer to choose colors to be used in the design.

Requirements
Must have
• my logo
Should not have
• Cursive lettering

```html
<!DOCTYPE html>
<html lang="en">
<head>
<meta charset="utf-8">
<title>Birchway Canine Training – Business Card</title>
<link rel="stylesheet" href="https://fonts.googleapis.com/css2?family=Montserrat:wght@600;700&family=Quicksand:wght@500;600&display=swap">
<style>
  :root {
    --backdrop: #c6c6c8;
    --card: #f3f3f3;
    --band: #6e7078;
    --ink: #1c1c1c;
    --rule: #6a6a6a;
  }
  * { box-sizing: border-box; margin: 0; padding: 0; }
  html, body { width: 1200px; height: 1200px; overflow: hidden; }
  body {
    background: var(--backdrop);
    position: relative;
    font-family: "Quicksand", sans-serif;
    color: var(--ink);
  }
  .card {
    position: absolute;
    left: 250px;
    width: 700px;
    height: 400px;
    background: var(--card);
    overflow: hidden;
  }
  .card--front { top: 150px; }
  .card--back { top: 630px; }

  .band { position: absolute; background: var(--band); height: 44px; }
  .band--top { top: 0; left: 0; width: 304px; }
  .band--bottom { bottom: 0; right: 0; width: 302px; }

  .brand {
    position: absolute;
    display: flex;
    align-items: center;
    gap: 10px;
    font-family: "Montserrat", sans-serif;
    font-weight: 700;
    color: var(--ink);
    text-transform: uppercase;
    line-height: 1.1;
  }
  .brand__dot {
    width: 26px; height: 26px;
    border-radius: 50%;
    background: var(--ink);
    flex: none;
  }
  .brand__name { font-size: 20px; letter-spacing: 0.5px; }
  .card--front .brand { left: 118px; top: 156px; }
  .card--back .brand { left: 46px; top: 230px; }

  .divider {
    position: absolute;
    left: 350px; top: 130px;
    width: 2px; height: 140px;
    background: var(--rule);
  }
  .contact { position: absolute; left: 383px; top: 138px; }
  .contact__name {
    font-family: "Montserrat", sans-serif;
    font-weight: 600;
    font-size: 19px;
    letter-spacing: 0.3px;
    margin-bottom: 22px;
  }
  .contact__line { font-size: 18px; font-weight: 500; line-height: 28px; }

  .back__web {
    position: absolute;
    left: 46px; top: 332px;
    font-size: 18px; font-weight: 600;
  }
</style>
</head>
<body>
  <section class="card card--front">
    <div class="band band--top"></div>
    <div class="band band--bottom"></div>
    <div class="brand">
      <span class="brand__dot"></span>
      <span class="brand__name">Birchway<br>Canine<br>Training</span>
    </div>
    <div class="divider"></div>
    <div class="contact">
      <p class="contact__name">LOWELL SPRATT</p>
      <p class="contact__line">281-904-3376</p>
      <p class="contact__line">info@birchwaycanine.example</p>
      <p class="contact__line">www.birchwaycanine.example</p>
    </div>
  </section>

  <section class="card card--back">
    <div class="brand">
      <span class="brand__dot"></span>
      <span class="brand__name">Birchway<br>Canine<br>Training</span>
    </div>
    <p class="back__web">www.birchwaycanine.example</p>
  </section>
</body>
</html>
```